Registration Page - Webinar

I need some proposition for a high conversion landing page for a Webinar.
This LP should follow some (minimal) rules:
1 - We need to have a registration box at it
2 - 1, 2 or 3 Keynote Speakers
3 - Featuring Time & Date
4 - All webinars will be free
5 - Title of the webinar
6 - Description of the webinar
7 - Should harmonize with my home page colors (www.themaplehearth.com)

```html
<!DOCTYPE html>
<html lang="en">
<head>
<meta charset="utf-8">
<title>The Maple Hearth – Webinar Registration</title>
<link rel="stylesheet" href="https://fonts.googleapis.com/css2?family=Barlow:wght@400;500&family=Poppins:wght@400;500;600;700&family=Rubik:wght@400&display=swap">
<style>
:root{
  --pink:#dc0063;
  --teal:#1696b4;
  --navy:#2c1b5c;
  --green:#1ea52e;
  --dark:#1b1b1d;
  --text:#444;
  --white:#fff;
}
*{box-sizing:border-box;margin:0;padding:0}
html,body{width:1200px;height:2244px;overflow:hidden;background:var(--white)}
body{position:relative;font-family:'Rubik',sans-serif;color:var(--text)}
.abs{position:absolute}
.topbar{left:0;top:0;width:1200px;height:54px;background:var(--pink)}
.nav{left:124px;top:0;height:54px;display:flex;align-items:center;gap:29px;font:500 11.5px 'Poppins',sans-serif;color:var(--white)}
.social{right:131px;top:22px;display:flex;gap:16px}
.social span{width:12px;height:12px;border-radius:50%;background:var(--white);display:block}
.header{left:0;top:54px;width:1200px;height:81px;background:var(--white);box-shadow:0 1px 2px rgba(0,0,0,.15);z-index:2}
.logo-bump{left:512px;top:100px;width:176px;height:66px;border-radius:0 0 88px 88px;background:var(--white);z-index:3}
.brand{left:450px;top:84px;width:300px;text-align:center;font:700 28px/1 'Poppins',sans-serif;color:var(--navy);z-index:4}
.wa-pill{display:flex;align-items:center;gap:7px;background:var(--green);color:var(--white);font:600 12.5px 'Barlow',sans-serif;border-radius:3px}
.wa-pill i{width:14px;height:14px;border-radius:50%;border:2px solid var(--white);display:block}
.header .wa-pill{position:absolute;left:175px;top:18px;width:176px;height:24px;padding-left:8px}
.phones{display:flex;gap:18px;font:400 12.5px 'Barlow',sans-serif;color:var(--navy)}
.phones span{display:flex;align-items:center;gap:5px}
.flag{width:17px;height:12px;border-radius:2px;display:inline-block}
.flag.br{background:var(--green)}
.flag.us{background:linear-gradient(#c0283c 50%,#3d4c9a 50%)}
.header .phones{position:absolute;left:125px;top:50px}
.cta{display:flex;align-items:center;gap:7px;color:var(--navy);font:600 11.5px/1 'Poppins',sans-serif;text-transform:uppercase}
.cta svg{flex:none}
.header .cta-agent{position:absolute;left:779px;top:24px}
.header .cta-schedule{position:absolute;left:933px;top:24px}
.hero{left:0;top:135px;width:1200px;height:913px;overflow:hidden}
.hero-photo{position:absolute;inset:0;background:linear-gradient(180deg,#2d4f77 0%,#27476a 35%,#4a4c5e 58%,#8a6a45 72%,#3c3a3c 85%,#2a2f38 100%)}
.hero-title{position:absolute;top:275px;width:1200px;text-align:center;font:500 45px/1.25 'Barlow',sans-serif;color:var(--white);text-transform:uppercase}
.hero-title .big{display:block;font-size:57px;line-height:1.15}
.btn{display:flex;align-items:center;justify-content:center;background:var(--pink);color:var(--white);font:500 21px 'Barlow',sans-serif;text-transform:uppercase}
.hero .read-more{position:absolute;left:508px;top:416px;width:184px;height:54px}
.hero-curve{position:absolute;left:0;top:0}
.reg-title{position:absolute;top:688px;width:1200px;text-align:center;font:400 31px 'Barlow',sans-serif;color:var(--white);letter-spacing:.5px}
.rule{position:absolute;height:2px;width:56px}
.reg-title-rule{left:572px;top:736px;background:var(--white)}
.reg-form{position:absolute;left:119px;top:767px;display:flex;gap:6px}
.field{width:236px;height:41px;background:var(--white);font:400 13px 'Rubik',sans-serif;color:#333;padding:13px 11px 0}
.hero .register{position:absolute;left:514px;top:834px;width:173px;height:47px;font-size:19px}
.section-title{top:1112px;width:1200px;text-align:center;font:400 31px 'Barlow',sans-serif;color:#333}
.title-rule{left:570px;top:1161px;width:60px;background:var(--pink)}
.card{width:312px;height:480px}
.card-photo{position:absolute;left:0;top:0;width:312px;height:308px;background:linear-gradient(160deg,#8c8a86,#5d5752 60%,#3f3a37)}
.card-body{position:absolute;left:12px;top:265px;width:288px;height:210px;background:var(--white);text-align:center}
.ribbon{position:absolute;left:0;top:0}
.speaker-name{margin-top:23px;font:400 20px 'Barlow',sans-serif;color:#333;text-transform:uppercase}
.card-body .name-rule{width:32px;height:2px;background:var(--pink);margin:10px auto 9px}
.bio{font:400 13px/25px 'Rubik',sans-serif;color:#555;padding:0 26px}
.card-body hr{border:0;border-top:1px solid #ddd;width:222px;margin:15px auto 0}
.when{margin-top:18px;font:500 14.5px 'Barlow',sans-serif}
.when.green{color:var(--green)}
.when.pink{color:var(--pink)}
.footer{left:0;top:1770px;width:1200px;height:416px;background:linear-gradient(180deg,#fff 0%,#e9e9ec 22%,#f4f4f6 60%,#fff 100%);overflow:hidden}
.skyline{position:absolute;left:0;top:0}
.office{position:absolute;left:111px;width:320px;color:var(--navy)}
.office h3{display:flex;align-items:center;gap:8px;font:700 16px 'Poppins',sans-serif}
.office p{font:400 12px/20px 'Poppins',sans-serif;padding-top:4px}
.email{position:absolute;left:111px;top:360px;display:flex;align-items:center;gap:7px;font:700 16px 'Poppins',sans-serif;color:var(--navy)}
.footer-brand{position:absolute;left:440px;top:172px;width:320px;text-align:center;font:700 36px/1 'Poppins',sans-serif;color:var(--navy)}
.footer .wa-pill{position:absolute;left:805px;top:117px;width:256px;height:33px;padding-left:10px;font-size:19px;gap:12px}
.footer .wa-pill i{width:18px;height:18px}
.footer .phones{position:absolute;left:788px;top:164px;font-size:14px;gap:12px}
.footer .cta{font-size:15px;line-height:1.3;gap:8px}
.footer .cta-agent{position:absolute;left:780px;top:212px}
.footer .cta-schedule{position:absolute;left:935px;top:212px}
.bottombar{left:0;top:2186px;width:1200px;height:58px;background:var(--dark);color:var(--white);font:400 11.5px 'Poppins',sans-serif}
.copyright{position:absolute;left:111px;top:20px}
.copyright em{font-style:normal;color:var(--pink)}
.bottom-nav{position:absolute;right:48px;top:21px;display:flex;gap:34px;font:600 10.5px 'Poppins',sans-serif;text-transform:uppercase}
.bottom-nav .active{color:var(--pink);font-weight:400}
</style>
</head>
<body>

<div class="abs topbar">
  <nav class="abs nav"><span>HOME</span><span>SOBRE NÓS</span><span>PORTIFÓLIO</span><span>IMÓVEIS</span><span>NOTÍCIAS</span><span>EBOOKS</span><span>CONTATO</span></nav>
  <div class="abs social" aria-label="Social links"><span></span><span></span><span></span></div>
</div>

<header class="abs header">
  <div class="wa-pill"><i></i>EUA +(407) 555-0142</div>
  <div class="phones"><span><b class="flag br"></b>+55 21 5550-1270</span><span><b class="flag us"></b>+1 (855)555-0187</span></div>
  <div class="cta cta-agent">
    <svg width="38" height="38" viewBox="0 0 38 38"><circle cx="19" cy="19" r="19" fill="#dc0063"/><path d="M11 12h16v10h-9l-4 4v-4h-3z" fill="none" stroke="#fff" stroke-width="1.6"/></svg>
    <span>Fale com um<br>agente</span>
  </div>
  <div class="cta cta-schedule">
    <svg width="38" height="38" viewBox="0 0 38 38"><circle cx="19" cy="19" r="19" fill="#1696b4"/><rect x="11" y="12" width="16" height="14" rx="2" fill="none" stroke="#fff" stroke-width="1.6"/><path d="M11 16h16M15 19h1M19 19h1M23 19h1M15 22h1M19 22h1M23 22h1" stroke="#fff" stroke-width="1.6"/></svg>
    <span>Agende uma<br>conversa</span>
  </div>
</header>
<div class="abs logo-bump"></div>
<div class="abs brand">Maple Hearth</div>

<section class="abs hero">
  <div class="hero-photo" role="img" aria-label="City skyline with glass towers and palm trees along the waterfront at dusk"></div>
  <h1 class="hero-title">Live Florida &amp;<span class="big">Get Freedom to Dream</span></h1>
  <div class="btn read-more">Read More</div>
  <svg class="hero-curve" width="1200" height="913" viewBox="0 0 1200 913">
    <path d="M0 770 Q600 550 1200 770 L1200 913 L0 913 Z" fill="#dc0063"/>
    <path d="M0 800 Q600 500 1200 800 L1200 913 L0 913 Z" fill="#1696b4" fill-opacity=".96"/>
  </svg>
  <h2 class="reg-title">REGISTRATION</h2>
  <div class="rule reg-title-rule"></div>
  <form class="reg-form">
    <div class="field">Name :</div>
    <div class="field">Email :</div>
    <div class="field">Password :</div>
    <div class="field">Confirm Password :</div>
  </form>
  <div class="btn register">Register Now</div>
</section>

<h2 class="abs section-title">OUR SPEAKERS</h2>
<div class="abs rule title-rule"></div>

<article class="abs card" style="left:111px;top:1196px">
  <div class="card-photo" role="img" aria-label="Portrait of a smiling male speaker"></div>
  <div class="card-body">
    <svg class="ribbon" width="100" height="80" viewBox="0 0 100 80"><polygon points="0,0 96,0 0,80" fill="#dc0063"/><text x="34" y="46" transform="rotate(-40 34 46)" fill="#fff" font-family="Barlow,sans-serif" font-size="17">FREE</text></svg>
    <div class="speaker-name">Alex Moreno</div>
    <div class="name-rule"></div>
    <p class="bio">Sed ut perspiciatis unde omnis iste natus error sit voluptatem accusantium doloremque laudantium</p>
    <hr>
    <p class="when green">04 Apr 2020 &nbsp;/&nbsp; 8:00am to 8:00pm</p>
  </div>
</article>

<article class="abs card" style="left:444px;top:1196px">
  <div class="card-photo" role="img" aria-label="Portrait of a smiling female speaker" style="background:linear-gradient(160deg,#9a9690,#6d655c 60%,#4a423a)"></div>
  <div class="card-body">
    <svg class="ribbon" width="100" height="80" viewBox="0 0 100 80"><polygon points="0,0 96,0 0,80" fill="#dc0063"/><text x="34" y="46" transform="rotate(-40 34 46)" fill="#fff" font-family="Barlow,sans-serif" font-size="17">FREE</text></svg>
    <div class="speaker-name">Alex Moreno</div>
    <div class="name-rule"></div>
    <p class="bio">Sed ut perspiciatis unde omnis iste natus error sit voluptatem accusantium doloremque laudantium</p>
    <hr>
    <p class="when pink">04 Apr 2020 &nbsp;/&nbsp; 8:00am to 8:00pm</p>
  </div>
</article>

<article class="abs card" style="left:777px;top:1196px">
  <div class="card-photo" role="img" aria-label="Portrait of a smiling male speaker wearing glasses" style="background:linear-gradient(160deg,#a5a39f,#807b75 60%,#5d5852)"></div>
  <div class="card-body">
    <svg class="ribbon" width="100" height="80" viewBox="0 0 100 80"><polygon points="0,0 96,0 0,80" fill="#dc0063"/><text x="34" y="46" transform="rotate(-40 34 46)" fill="#fff" font-family="Barlow,sans-serif" font-size="17">FREE</text></svg>
    <div class="speaker-name">Alex Moreno</div>
    <div class="name-rule"></div>
    <p class="bio">Sed ut perspiciatis unde omnis iste natus error sit voluptatem accusantium doloremque laudantium</p>
    <hr>
    <p class="when green">04 Apr 2020 &nbsp;/&nbsp; 8:00am to 8:00pm</p>
  </div>
</article>

<footer class="abs footer">
  <svg class="skyline" width="1200" height="110" viewBox="0 0 1200 110" role="img" aria-label="Faint city skyline silhouette">
    <defs><linearGradient id="sky" x1="0" y1="0" x2="0" y2="1"><stop offset="0" stop-color="#e4e4e8" stop-opacity=".4"/><stop offset="1" stop-color="#dcdce0"/></linearGradient></defs>
    <rect x="0" y="40" width="1200" height="70" fill="url(#sky)"/>
  </svg>

  <div class="office" style="top:118px">
    <h3><svg width="10" height="14" viewBox="0 0 10 14"><path d="M5 0a5 5 0 0 1 5 5c0 4-5 9-5 9S0 9 0 5a5 5 0 0 1 5-5z" fill="#dc0063"/><circle cx="5" cy="5" r="2" fill="#fff"/></svg>Harbor Point Center</h3>
    <p>2nd Floor, Av. Atlântica Norte 1200,<br>Bairro Azul - RJ - Brazil</p>
  </div>
  <div class="office" style="top:196px">
    <h3><svg width="10" height="14" viewBox="0 0 10 14"><path d="M5 0a5 5 0 0 1 5 5c0 4-5 9-5 9S0 9 0 5a5 5 0 0 1 5-5z" fill="#dc0063"/><circle cx="5" cy="5" r="2" fill="#fff"/></svg>Linden Park Mall</h3>
    <p>Rua das Palmeiras, 3140 Sala 12, Jardim<br>Verde - São Paulo - Brazil</p>
  </div>
  <div class="office" style="top:274px">
    <h3><svg width="10" height="14" viewBox="0 0 10 14"><path d="M5 0a5 5 0 0 1 5 5c0 4-5 9-5 9S0 9 0 5a5 5 0 0 1 5-5z" fill="#dc0063"/><circle cx="5" cy="5" r="2" fill="#fff"/></svg>Lakeside Office</h3>
    <p>4120 Sunbay Avenue, Suite 210, Lakeside,<br>USA</p>
  </div>
  <div class="email"><svg width="17" height="12" viewBox="0 0 17 12"><rect width="17" height="12" rx="1" fill="#dc0063"/><path d="M1 1l7.5 6L16 1" fill="none" stroke="#fff" stroke-width="1.4"/></svg>hello@themaplehearth.com</div>

  <div class="footer-brand">Maple Hearth</div>

  <div class="wa-pill"><i></i>US + (407) 555-0142</div>
  <div class="phones"><span><b class="flag br"></b>+55 21 5550-1270</span><span><b class="flag us"></b>+1 (855)555-0187</span></div>
  <div class="cta cta-agent">
    <svg width="38" height="38" viewBox="0 0 38 38"><circle cx="19" cy="19" r="19" fill="#dc0063"/><path d="M11 12h16v10h-9l-4 4v-4h-3z" fill="none" stroke="#fff" stroke-width="1.6"/></svg>
    <span>Talk to an<br>agent</span>
  </div>
  <div class="cta cta-schedule">
    <svg width="38" height="38" viewBox="0 0 38 38"><circle cx="19" cy="19" r="19" fill="#1696b4"/><rect x="11" y="12" width="16" height="14" rx="2" fill="none" stroke="#fff" stroke-width="1.6"/><path d="M11 16h16M15 19h1M19 19h1M23 19h1M15 22h1M19 22h1M23 22h1" stroke="#fff" stroke-width="1.6"/></svg>
    <span>Schedule a<br>conversation</span>
  </div>
</footer>

<div class="abs bottombar">
  <p class="copyright">© 2020 - THE MAPLE HEARTH BY <em>NORTHBEAM STUDIO</em></p>
  <nav class="bottom-nav"><span class="active">Home</span><span>Properties</span><span>News</span><span>Contact</span><span>Terms of Use</span></nav>
</div>

</body>
</html>
```